Crumb of Maple 2022- CW poster ads

Design for our Crumb of Maple Event
Designs 3 designs for Chirp Wall Banner, posts and social Media ads
Each can look the same just different subjects on each
1. Design We're Back!
The Crumb Of Maple Is Back!
Ventura County’s Premier Food, Wine and Brew Event
August 14th
Vendor and ticket info at https://brimfulmaplefq.com/

2. Vendors be a part of the event
The Crumb of Maple is Back!
August 14th 2020
Vendors sign up today at
Vendor info at https://brimfulmaplefq.com/

3. Sponsor info
The Crumb Of Maple
August 14th 2022
Check out our great Sponsorship opportunities
Sponsor info at https://brimfulmaplefq.com/

Target Market(s)

Foodies, wine and beer enthusists

Industry/Entity Type

Farm to fork, fresh in season and local

Colors
00AB8E
00BBA5
67D7C9
C6EFE9
E9F9F6

Requirements
Should not have
• no fast food looking photos

```html
<!DOCTYPE html>
<html lang="en">
<head>
<meta charset="utf-8">
<title>Crumb Of Maple – Sponsor Posters</title>
<link rel="stylesheet" href="https://fonts.googleapis.com/css2?family=Exo+2:wght@400;500;600&family=Lilita+One&family=Saira:wght@300&display=swap">
<style>
  :root {
    --teal-deep: #00AB8E;
    --teal: #00BBA5;
    --teal-soft: #67D7C9;
    --mint: #C6EFE9;
    --mist: #E9F9F6;
    --ink: #111111;
    --alert-red: #E8202A;
    --white: #ffffff;
    --food-board: #5b5a55;
    --food-grass: #93a86a;
    --food-chip: #d9883a;
    --food-glass: #efe8dc;
    --band-sky: #f4efe6;
    --band-plaid: #c0503a;
    --band-wood: #c59a63;
    --band-warm: #b5672e;
  }
  * { margin: 0; padding: 0; box-sizing: border-box; }
  html, body { width: 1200px; height: 826px; overflow: hidden; background: var(--white); }
  body { position: relative; font-family: "Exo 2", sans-serif; color: var(--ink); }

  .sheet-heading {
    position: absolute; left: 72px; width: 602px; top: 56px;
    text-align: center; font-family: "Saira", sans-serif; font-weight: 300;
    font-size: 40px; line-height: 54px; letter-spacing: 1px;
  }

  .poster { position: absolute; overflow: hidden;
    background: linear-gradient(180deg, var(--mist) 0%, var(--white) 45%, var(--mint) 100%); }
  .poster svg.art { position: absolute; inset: 0; }
  .poster .txt { position: absolute; white-space: nowrap; }

  .poster--square { left: 72px; top: 169px; width: 602px; height: 602px; }
  .poster--tall { left: 737px; top: 47px; width: 410px; height: 723px; }

  .event-title { font-weight: 500; font-size: 32px; line-height: 36px; }
  .event-tagline { font-weight: 500; font-size: 19px; line-height: 22px; }
  .brand-mark { display: flex; align-items: center; gap: 6px; font-weight: 600; font-size: 19px; }
  .brand-mark .dot { width: 14px; height: 14px; border-radius: 50%; background: var(--teal-deep); }
  .brand-mark--faint { opacity: .35; font-size: 14px; gap: 4px; }
  .brand-mark--faint .dot { width: 10px; height: 10px; }
  .brand-mark--small { font-size: 12px; }

  .event-date { font-family: "Lilita One", sans-serif; line-height: 1; }
  .event-date .day { display: block; }
  .event-date--light { color: var(--white); }
  .event-date--red { color: var(--alert-red); }

  .sponsor-lead { font-size: 17px; line-height: 20px; }
  .sponsor-lead--red { color: var(--alert-red); font-weight: 500; }
  .sponsor-pitch { font-weight: 500; font-size: 24px; line-height: 23px; }
  .sponsor-link { font-size: 17px; line-height: 22px; }
</style>
</head>
<body>

<h1 class="sheet-heading">DESIGN NUMBER (2) TWO<br>FOR SPONSORS</h1>

<section class="poster poster--square">
  <svg class="art" width="602" height="602" viewBox="0 0 602 602">
    <defs>
      <pattern id="stripeSq" width="6" height="6" patternUnits="userSpaceOnUse" patternTransform="rotate(45)">
        <rect width="3" height="6" fill="var(--teal-soft)"/>
      </pattern>
      <linearGradient id="foodSq" x1="0" y1="0" x2="0.35" y2="1">
        <stop offset="0" stop-color="var(--food-board)"/>
        <stop offset="0.3" stop-color="var(--food-grass)"/>
        <stop offset="0.6" stop-color="var(--food-chip)"/>
        <stop offset="1" stop-color="var(--food-glass)"/>
      </linearGradient>
      <linearGradient id="bandSq" x1="0" y1="0" x2="0.4" y2="1">
        <stop offset="0" stop-color="var(--band-sky)"/>
        <stop offset="0.45" stop-color="var(--band-wood)"/>
        <stop offset="0.75" stop-color="var(--band-plaid)"/>
        <stop offset="1" stop-color="var(--band-warm)"/>
      </linearGradient>
    </defs>
    <circle class="stripe-disc" cx="38" cy="35" r="22" fill="url(#stripeSq)"/>
    <rect class="date-band" x="0" y="235" width="28" height="131" fill="var(--teal-deep)"/>
    <rect class="date-band" x="126" y="235" width="476" height="131" fill="var(--teal-deep)"/>

    <g class="feature-ring">
      <circle cx="300" cy="301" r="137" fill="var(--mist)"/>
      <circle cx="300" cy="301" r="134" fill="var(--teal-deep)"/>
      <path d="M230 201 A122 122 0 0 1 370 201" stroke="var(--white)" stroke-width="3" fill="none" stroke-linecap="round"/>
      <path d="M230 401 A122 122 0 0 0 370 401" stroke="var(--white)" stroke-width="3" fill="none" stroke-linecap="round"/>
      <path d="M372 215 A112 112 0 0 1 372 387" stroke="var(--white)" stroke-width="3" fill="none" stroke-dasharray="6 5"/>
      <path d="M228 215 A112 112 0 0 0 228 387" stroke="var(--white)" stroke-width="3" fill="none" stroke-dasharray="6 5"/>
      <circle cx="300" cy="301" r="108" fill="var(--white)"/>
      <circle cx="300" cy="301" r="104" fill="url(#foodSq)" role="img" aria-label="Photo of ceviche served in glasses with tortilla chips at an outdoor food stand"/>
    </g>

    <circle cx="428" cy="197" r="8" fill="none" stroke="var(--ink)" stroke-width="3"/>
    <path d="M172 407 l12 12 M184 407 l-12 12" stroke="var(--ink)" stroke-width="3"/>
    <g class="dot-grid" fill="var(--ink)">
      <circle cx="64" cy="266" r="2.6"/><circle cx="77" cy="266" r="2.6"/>
      <circle cx="64" cy="278" r="2.6"/><circle cx="77" cy="278" r="2.6"/>
      <circle cx="64" cy="290" r="2.6"/><circle cx="77" cy="290" r="2.6"/>
      <circle cx="64" cy="302" r="2.6"/><circle cx="77" cy="302" r="2.6"/>
      <circle cx="64" cy="314" r="2.6"/><circle cx="77" cy="314" r="2.6"/>
      <circle cx="64" cy="326" r="2.6"/><circle cx="77" cy="326" r="2.6"/>
      <circle cx="64" cy="338" r="2.6"/><circle cx="77" cy="338" r="2.6"/>
    </g>
    <g class="dot-row" fill="var(--ink)">
      <circle cx="64" cy="550" r="2.4"/><circle cx="72" cy="550" r="2.4"/><circle cx="80" cy="550" r="2.4"/><circle cx="88" cy="550" r="2.4"/><circle cx="96" cy="550" r="2.4"/><circle cx="104" cy="550" r="2.4"/><circle cx="112" cy="550" r="2.4"/><circle cx="120" cy="550" r="2.4"/>
      <circle cx="64" cy="560" r="2.4"/><circle cx="72" cy="560" r="2.4"/><circle cx="80" cy="560" r="2.4"/><circle cx="88" cy="560" r="2.4"/><circle cx="96" cy="560" r="2.4"/><circle cx="104" cy="560" r="2.4"/><circle cx="112" cy="560" r="2.4"/><circle cx="120" cy="560" r="2.4"/>
    </g>

    <path class="band-photo" d="M364 602 Q372 470 470 428 Q540 398 602 372 L602 602 Z" fill="url(#bandSq)" role="img" aria-label="Photo of musicians playing guitars on an outdoor stage"/>
    <path d="M356 602 Q364 462 464 420 Q540 388 602 362" stroke="var(--teal)" stroke-width="5" fill="none"/>
  </svg>

  <h2 class="txt event-title" style="left:62px; top:80px;">The Crumb Of Maple</h2>
  <p class="txt event-tagline" style="left:62px; top:120px;">Ventura County’s Premier Food,<br>Wine and Brew Event</p>
  <div class="txt brand-mark" style="left:396px; top:108px;"><span class="dot"></span>Brimful Maple</div>
  <div class="txt brand-mark brand-mark--faint" style="left:478px; top:440px;"><span class="dot"></span>Brimful Maple</div>

  <p class="txt event-date event-date--light" style="left:450px; top:258px;">
    <span class="day" style="font-size:54px;">14th</span>
    <span class="day" style="font-size:25px; margin-top:2px;">Aug. 2022</span>
  </p>

  <p class="txt sponsor-lead" style="left:62px; top:456px;">Check out our</p>
  <p class="txt sponsor-pitch" style="left:62px; top:474px;">great Sponsorship<br>opportunities @</p>
  <p class="txt sponsor-link" style="left:62px; top:521px;">https://brimfulmaplefq.com/</p>
</section>

<section class="poster poster--tall">
  <svg class="art" width="410" height="723" viewBox="0 0 410 723">
    <defs>
      <pattern id="stripeTall" width="5" height="5" patternUnits="userSpaceOnUse" patternTransform="rotate(45)">
        <rect width="2.5" height="5" fill="var(--teal-soft)"/>
      </pattern>
      <linearGradient id="foodTall" x1="0" y1="0" x2="0.35" y2="1">
        <stop offset="0" stop-color="var(--food-board)"/>
        <stop offset="0.3" stop-color="var(--food-grass)"/>
        <stop offset="0.6" stop-color="var(--food-chip)"/>
        <stop offset="1" stop-color="var(--food-glass)"/>
      </linearGradient>
      <linearGradient id="bandTall" x1="0" y1="0" x2="0.3" y2="1">
        <stop offset="0" stop-color="var(--band-sky)"/>
        <stop offset="0.4" stop-color="var(--band-wood)"/>
        <stop offset="0.75" stop-color="var(--band-plaid)"/>
        <stop offset="1" stop-color="var(--band-warm)"/>
      </linearGradient>
    </defs>
    <circle cx="363" cy="32" r="14" fill="url(#stripeTall)"/>

    <path class="band-photo" d="M192 513 L410 513 L410 630 L168 630 Q172 562 192 513 Z" fill="url(#bandTall)" role="img" aria-label="Photo of musicians performing with guitars and microphones outdoors"/>
    <path d="M403 395 Q260 450 200 500 Q168 550 162 630" stroke="var(--teal)" stroke-width="5" fill="none"/>

    <g class="feature-ring">
      <circle cx="218" cy="370" r="137" fill="var(--mist)"/>
      <circle cx="218" cy="370" r="134" fill="var(--teal-deep)"/>
      <path d="M148 270 A122 122 0 0 1 288 270" stroke="var(--white)" stroke-width="3" fill="none" stroke-linecap="round"/>
      <path d="M148 470 A122 122 0 0 0 288 470" stroke="var(--white)" stroke-width="3" fill="none" stroke-linecap="round"/>
      <path d="M290 284 A112 112 0 0 1 290 456" stroke="var(--white)" stroke-width="3" fill="none" stroke-dasharray="6 5"/>
      <path d="M146 284 A112 112 0 0 0 146 456" stroke="var(--white)" stroke-width="3" fill="none" stroke-dasharray="6 5"/>
      <circle cx="218" cy="370" r="108" fill="var(--white)"/>
      <circle cx="218" cy="370" r="104" fill="url(#foodTall)" role="img" aria-label="Photo of ceviche served in glasses with tortilla chips at an outdoor food stand"/>
    </g>

    <circle cx="344" cy="266" r="8" fill="none" stroke="var(--ink)" stroke-width="3"/>
    <path d="M88 475 l12 12 M100 475 l-12 12" stroke="var(--ink)" stroke-width="3"/>
    <g class="dot-grid" fill="var(--ink)">
      <circle cx="46" cy="335" r="2.6"/><circle cx="59" cy="335" r="2.6"/>
      <circle cx="46" cy="346" r="2.6"/><circle cx="59" cy="346" r="2.6"/>
      <circle cx="46" cy="357" r="2.6"/><circle cx="59" cy="357" r="2.6"/>
      <circle cx="46" cy="368" r="2.6"/><circle cx="59" cy="368" r="2.6"/>
      <circle cx="46" cy="380" r="2.6"/><circle cx="59" cy="380" r="2.6"/>
      <circle cx="46" cy="391" r="2.6"/><circle cx="59" cy="391" r="2.6"/>
      <circle cx="46" cy="403" r="2.6"/><circle cx="59" cy="403" r="2.6"/>
    </g>
    <g class="dot-row" fill="var(--ink)">
      <circle cx="286" cy="687" r="2.4"/><circle cx="293" cy="687" r="2.4"/><circle cx="300" cy="687" r="2.4"/><circle cx="307" cy="687" r="2.4"/><circle cx="314" cy="687" r="2.4"/><circle cx="321" cy="687" r="2.4"/><circle cx="328" cy="687" r="2.4"/><circle cx="335" cy="687" r="2.4"/>
      <circle cx="286" cy="696" r="2.4"/><circle cx="293" cy="696" r="2.4"/><circle cx="300" cy="696" r="2.4"/><circle cx="307" cy="696" r="2.4"/><circle cx="314" cy="696" r="2.4"/><circle cx="321" cy="696" r="2.4"/><circle cx="328" cy="696" r="2.4"/><circle cx="335" cy="696" r="2.4"/>
    </g>
  </svg>

  <div class="txt brand-mark" style="left:140px; top:66px;"><span class="dot"></span>Brimful Maple</div>
  <div class="txt brand-mark brand-mark--faint brand-mark--small" style="left:308px; top:482px;"><span class="dot"></span>Brimful Maple</div>

  <h2 class="txt event-title" style="left:0; width:410px; text-align:center; top:136px;">The Crumb Of Maple</h2>
  <p class="txt event-tagline" style="left:0; width:410px; text-align:center; top:176px; white-space:normal;">Ventura County’s Premier Food,<br>Wine and Brew Event</p>

  <p class="txt event-date event-date--red" style="left:43px; top:542px;">
    <span class="day" style="font-size:44px;">14th</span>
    <span class="day" style="font-size:21px; margin-top:1px;">Aug. 2022</span>
  </p>

  <p class="txt sponsor-lead sponsor-lead--red" style="left:44px; top:609px;">Check out our</p>
  <p class="txt sponsor-pitch" style="left:44px; top:630px;">great Sponsorship<br>opportunities @</p>
  <p class="txt sponsor-link" style="left:44px; top:678px;">https://brimfulmaplefq.com/</p>
</section>

</body>
</html>
```